Simple landing page for Brambles cookbook

I need a one page landingpage where customers can order the cookbook.
This is a cookbook of a collection of recipes from our deli that we used to run.
I need a landing page where customers can come and order the book. I also need it coded. I already have the domain through hostwell.
I can send the file of the book through wetransfer. It's too big to upload here. Just so you get the feel that I am looking for.
I attached a simple text as an introduction to the page. But I am open to any suggestions. I want it all to be about the experience that we are sharing the recipes with everybody and that it's for sale. The book is $29.99, shipping included.
Customers have to be able to click and buy the book from it.

Coding

Coded - Design and coding required

Number of Pages Required

1 page

Font styles to use
Sans Serif

Requirements
Must have
• Same colors as the cookbook

```html
<!DOCTYPE html>
<html lang="en">
<head>
<meta charset="utf-8">
<title>Brambles Sandwiches – Your Favorite Recipes In One Book</title>
<link href="https://fonts.googleapis.com/css2?family=Oswald:wght@500;600&family=Poppins:wght@400;500&display=swap" rel="stylesheet">
<style>
:root{
  --pink:#c5175a;
  --brown-dark:#3a2720;
  --peach:#e9a86c;
  --orange:#d9731f;
  --ink:#2e2420;
  --partner-grey:#b9b9b9;
}
*{box-sizing:border-box;margin:0;padding:0}
html,body{width:1200px;height:3035px;overflow:hidden;background:#fff}
body{font-family:"Poppins",sans-serif;color:var(--ink)}
.page{position:relative;width:1200px;height:3035px;overflow:hidden;background:#fff}
.abs{position:absolute}
.heading{font-family:"Oswald",sans-serif;font-weight:600;text-transform:uppercase;letter-spacing:2px}
.btn{position:absolute;display:flex;align-items:center;gap:12px;height:46px;padding:0 22px 0 7px;border-radius:23px;background:var(--pink);color:#fff;text-decoration:none;font-family:"Oswald",sans-serif;font-weight:500;font-size:20px;letter-spacing:2px;text-transform:uppercase;white-space:nowrap}
.btn .arrow{flex:none;width:32px;height:32px;border-radius:50%;background:#fff;display:flex;align-items:center;justify-content:center}
.ph{position:absolute}

/* hero */
.hero-bg{position:absolute;left:0;top:0;width:1200px;height:621px;background:linear-gradient(180deg,#2a1a12 0%,#3b2416 45%,#6a3f1f 75%,#b06a2c 90%,#7a4720 100%)}
.logo-blob{position:absolute;left:0;top:0}
.logo{position:absolute;left:148px;top:28px;font-family:"Oswald",sans-serif;font-weight:600;color:var(--brown-dark);line-height:1;text-transform:uppercase}
.logo-name{font-size:40px;letter-spacing:1px}
.logo-tag{font-size:19px;letter-spacing:1px;margin-top:4px}
.hero-title{position:absolute;left:145px;top:170px;width:560px;color:#fff;font-size:50px;line-height:57px;letter-spacing:3px;white-space:nowrap}
.hero-sub{position:absolute;left:145px;top:297px;width:420px;color:#fff;font-size:13px;line-height:19px;letter-spacing:1.2px}
.hero-includes{position:absolute;left:145px;top:348px;color:#fff;font-size:17px;letter-spacing:1.5px;font-weight:500;white-space:nowrap}
.hero-includes span{color:var(--pink);font-size:21px}
.hero-cats{position:absolute;left:148px;top:385px;display:flex;gap:30px;color:#fff;font-size:13px;letter-spacing:1px}
.hero-cats div{display:flex;align-items:center;gap:7px}
.badge-text{position:absolute;color:#fff;text-align:center;font-family:"Oswald",sans-serif;font-weight:500}
.badge-text .price{font-size:32px;letter-spacing:1px;line-height:1}
.badge-text .price small{font-size:17px}
.badge-text .ship{font-family:"Poppins",sans-serif;font-size:10px;line-height:11px;letter-spacing:.5px;margin-top:4px}

.partner-row{position:absolute;top:690px;left:0;width:1200px;display:flex;justify-content:center;gap:60px;align-items:center}
.partner{background:var(--partner-grey);border-radius:6px;height:34px}

/* feature card */
.card-photo{left:145px;top:780px;width:458px;height:680px;border-radius:10px 0 0 10px;background:radial-gradient(ellipse at 45% 45%,#e8c070 0%,#c9903e 35%,#6b6a3a 70%,#3d3a25 100%)}
.card-panel{position:absolute;left:603px;top:780px;width:452px;height:648px;border-radius:0 10px 10px 0;background:linear-gradient(180deg,#b8865c 0%,#7c5638 50%,#3c2a20 100%)}
.card-panel .item{position:absolute;left:34px;width:390px;color:#fff}
.card-panel h3{font-size:24px;letter-spacing:2.5px;margin-bottom:12px;white-space:nowrap}
.card-panel p{font-size:13px;line-height:19px;letter-spacing:1px}
.quote{position:absolute;left:279px;top:1371px;width:642px;height:134px;background:#fff;border-radius:12px;box-shadow:0 10px 30px rgba(0,0,0,.15);display:flex;align-items:center;justify-content:center;text-align:center;font-size:17px;line-height:29px;letter-spacing:1px;padding-top:18px}
.quote-mark{position:absolute;left:569px;top:1340px;width:62px;height:62px;border-radius:50%;background:var(--pink);display:flex;align-items:center;justify-content:center}

/* story */
.eyebrow{color:var(--pink);font-size:13px;letter-spacing:1px}
.story-item{position:absolute;left:160px;width:420px}
.story-item h3{font-size:24px;letter-spacing:2.5px;color:var(--ink);margin:4px 0 12px;white-space:nowrap}
.story-item p{font-size:13px;line-height:19px;letter-spacing:1px}

/* promo band */
.promo-title{position:absolute;left:600px;top:2205px;width:496px;text-align:center;color:#fff;font-size:47px;line-height:52px;letter-spacing:4px}
.promo-sub{position:absolute;left:600px;top:2318px;width:496px;text-align:center;color:#fff;font-size:13px;line-height:19px;letter-spacing:1.2px}

/* closing */
.closing-eyebrow{position:absolute;left:147px;top:2580px;color:var(--orange);font-size:20px;font-weight:500;letter-spacing:1px}
.closing-title{position:absolute;left:147px;top:2612px;color:var(--brown-dark);font-size:48px;letter-spacing:4px;white-space:nowrap}
.closing-text{position:absolute;left:147px;top:2700px;width:420px;font-size:16px;line-height:27px;letter-spacing:1.2px}
.copyright{position:absolute;left:0;top:2990px;width:1200px;text-align:center;font-size:14px;color:var(--ink)}
.copyright a{color:var(--ink)}
</style>
</head>
<body>
<main class="page">

  <!-- Hero -->
  <div class="hero-bg" role="img" aria-label="Dark rustic wooden table background"></div>
  <svg class="logo-blob" width="450" height="126" viewBox="0 0 450 126" aria-hidden="true">
    <path d="M0 0 H450 C380 40 330 110 250 122 C160 134 80 118 0 100 Z" fill="var(--peach)"/>
  </svg>
  <div class="logo">
    <div class="logo-name">Brambles</div>
    <div class="logo-tag">Sandwiches</div>
  </div>

  <h1 class="hero-title heading">Your Favorite<br>Recipes In One Book</h1>
  <p class="hero-sub">Surprise Family And Friends With Branded Sandwiches From Brambles</p>
  <div class="hero-includes">BOOK INCLUDES <span>28 RECIPES</span>:</div>
  <div class="hero-cats">
    <div><svg width="18" height="14" viewBox="0 0 18 14"><path d="M1 6 L9 1 L17 6 Z M1 8 H17 V12 H1 Z" fill="none" stroke="#fff" stroke-width="1.3"/></svg>Sandwiches</div>
    <div><svg width="18" height="14" viewBox="0 0 18 14"><path d="M2 5 H16 L13 12 H5 Z M5 5 L9 1" fill="none" stroke="#fff" stroke-width="1.3"/></svg>Sauces</div>
    <div><svg width="18" height="16" viewBox="0 0 18 16"><path d="M2 7 C2 2 16 2 16 7 Z M1 9 H17 M2 11 H16 V14 H2 Z" fill="none" stroke="#fff" stroke-width="1.3"/></svg>Burgers</div>
  </div>
  <a class="btn" href="#order" style="left:145px;top:430px">
    <span class="arrow"><svg width="16" height="14" viewBox="0 0 16 14"><path d="M1 7 H14 M8 1 L14 7 L8 13" fill="none" stroke="var(--pink)" stroke-width="2"/></svg></span>Order Now
  </a>
  <div class="ph" role="img" aria-label="Cheeseburger patty with melted cheese" style="left:-10px;top:458px;width:135px;height:100px;border-radius:50%;background:radial-gradient(ellipse at 50% 40%,#f0b53a 0%,#d89326 45%,#4a2e1f 80%)"></div>
  <div class="ph" role="img" aria-label="Brambles Sandwiches cookbook cover with a burger photo" style="left:725px;top:88px;width:323px;height:472px;border-radius:4px 10px 10px 4px;background:linear-gradient(180deg,#eef3f8 0%,#dde6ee 35%,#c98b4c 55%,#6e8a3c 70%,#e9edf2 88%);box-shadow:0 10px 30px rgba(0,0,0,.4)"></div>

  <svg class="abs" style="left:663px;top:163px" width="110" height="118" viewBox="0 0 110 118" aria-hidden="true">
    <g fill="var(--pink)">
      <circle cx="55" cy="59" r="44"/>
      <circle cx="55" cy="15" r="11"/><circle cx="77" cy="21" r="11"/><circle cx="93" cy="37" r="11"/><circle cx="99" cy="59" r="11"/><circle cx="93" cy="81" r="11"/><circle cx="77" cy="97" r="11"/><circle cx="55" cy="103" r="11"/><circle cx="33" cy="97" r="11"/><circle cx="17" cy="81" r="11"/><circle cx="11" cy="59" r="11"/><circle cx="17" cy="37" r="11"/><circle cx="33" cy="21" r="11"/>
    </g>
  </svg>
  <div class="badge-text" style="left:663px;top:203px;width:110px">
    <div class="price"><small>$</small>29.99</div>
    <div class="ship">Free<br>Shipping</div>
  </div>

  <!-- Partners -->
  <svg class="abs" style="left:472px;top:620px" width="256" height="28" viewBox="0 0 256 28" aria-hidden="true">
    <path d="M0 0 H256 C246 18 232 28 210 28 H46 C24 28 10 18 0 0 Z" fill="var(--brown-dark)"/>
  </svg>
  <div class="heading abs" style="left:472px;top:608px;width:256px;text-align:center;color:#fff;font-size:22px">Partners</div>
  <div class="partner-row" aria-label="Partner badges">
    <div class="partner" style="width:156px"></div>
    <div class="partner" style="width:118px;border-radius:17px"></div>
    <div class="partner" style="width:130px"></div>
    <div class="partner" style="width:124px"></div>
  </div>

  <!-- Feature card -->
  <div class="ph card-photo" role="img" aria-label="Grilled cheese panini being pulled apart with stretching cheese"></div>
  <div class="card-panel">
    <div class="item" style="top:76px">
      <h3 class="heading">Favorite Recipes In One Book</h3>
      <p>Lorem ipsum dolor sit amet, consectetur adipiscing elit. Magna pulvinar vestibulum bibendum dictum dignissim dictum auctor fusce eget.</p>
    </div>
    <div class="item" style="top:204px">
      <h3 class="heading">Favorite Recipes In One Book</h3>
      <p>Quis blandit sem viverra aliquam posuere risus semper eu. Faucibus mattis ipsum imperdiet molestie.</p>
    </div>
    <div class="item" style="top:334px">
      <h3 class="heading">Favorite Recipes In One Book</h3>
      <p>Dignissim ipsum vivamus sed habitant sed tincidunt nibh sed a. Tellus consequat adipiscing elit nisi. Eget in ullamcorper id pharetra, nisl.</p>
    </div>
  </div>
  <a class="btn" href="#order" style="left:637px;top:1243px">
    <span class="arrow"><svg width="16" height="14" viewBox="0 0 16 14"><path d="M1 7 H14 M8 1 L14 7 L8 13" fill="none" stroke="var(--pink)" stroke-width="2"/></svg></span>Order Now
  </a>
  <blockquote class="quote">We Truly Hope You Will Enjoy Making These Sandwiches<br>Just As Much As We Did.</blockquote>
  <div class="quote-mark"><svg width="30" height="22" viewBox="0 0 30 22"><path d="M8 2 A6 6 0 1 0 11 13 C10 17 7 19 4 20 M22 2 A6 6 0 1 0 25 13 C24 17 21 19 18 20" fill="none" stroke="#fff" stroke-width="2.6"/></svg></div>

  <!-- Story -->
  <div class="ph" role="img" aria-label="Hand holding a bitten burger" style="left:600px;top:1580px;width:600px;height:560px;background:radial-gradient(ellipse at 55% 45%,#b27a45 0%,#8a5a35 30%,#d6b9a0 55%,rgba(255,255,255,0) 75%)"></div>
  <div class="story-item" style="top:1645px">
    <div class="eyebrow">Lorem ipsum dolor</div>
    <h3 class="heading">Favorite Recipes In One Book</h3>
    <p>Lorem ipsum dolor sit amet, consectetur adipiscing elit. Magna pulvinar vestibulum bibendum dictum dignissim dictum auctor fusce eget.</p>
  </div>
  <div class="story-item" style="top:1808px">
    <div class="eyebrow">Lorem ipsum dolor</div>
    <h3 class="heading">Favorite Recipes In One Book</h3>
    <p>Quis blandit sem viverra aliquam posuere risus semper eu. Faucibus mattis ipsum imperdiet molestie.</p>
  </div>

  <!-- Promo band -->
  <svg class="abs" style="left:0;top:1900px" width="1200" height="600" viewBox="0 1900 1200 600" aria-hidden="true">
    <defs>
      <linearGradient id="bandFill" x1="0" y1="0" x2="1" y2="0">
        <stop offset="0" stop-color="#2c1f19"/>
        <stop offset=".6" stop-color="#4a3427"/>
        <stop offset="1" stop-color="#2a1d17"/>
      </linearGradient>
    </defs>
    <path d="M0 1915 C140 2050 340 2110 600 2115 C800 2118 1000 2100 1200 2080 V2490 C1050 2492 900 2490 760 2484 C450 2470 200 2400 0 2360 Z" fill="url(#bandFill)"/>
    <path d="M1005 2480 C1070 2460 1130 2445 1180 2425 C1130 2455 1080 2475 1005 2480 Z" fill="#fff"/>
  </svg>
  <div class="ph" role="img" aria-label="Two Brambles Sandwiches cookbooks standing at an angle" style="left:45px;top:1985px;width:580px;height:545px;background:linear-gradient(160deg,#e6edf3 0%,#cfdbe6 40%,#c88d52 58%,#6e8a3c 70%,#dfe7ee 90%);clip-path:polygon(8% 0,52% 4%,58% 18%,95% 14%,100% 98%,40% 100%,34% 48%,0 56%)"></div>
  <svg class="abs" style="left:800px;top:2085px" width="100" height="108" viewBox="0 0 110 118" aria-hidden="true">
    <g fill="var(--pink)">
      <circle cx="55" cy="59" r="44"/>
      <circle cx="55" cy="15" r="11"/><circle cx="77" cy="21" r="11"/><circle cx="93" cy="37" r="11"/><circle cx="99" cy="59" r="11"/><circle cx="93" cy="81" r="11"/><circle cx="77" cy="97" r="11"/><circle cx="55" cy="103" r="11"/><circle cx="33" cy="97" r="11"/><circle cx="17" cy="81" r="11"/><circle cx="11" cy="59" r="11"/><circle cx="17" cy="37" r="11"/><circle cx="33" cy="21" r="11"/>
    </g>
  </svg>
  <div class="badge-text" style="left:800px;top:2120px;width:100px">
    <div class="price" style="font-size:28px"><small>$</small>29.99</div>
    <div class="ship" style="font-size:9px;line-height:10px">Free<br>Shipping</div>
  </div>
  <h2 class="promo-title heading">Favorite Recipes<br>In One Book</h2>
  <p class="promo-sub">Surprise Family And Friends With Branded<br>Sandwiches From Brambles</p>
  <a class="btn" id="order" href="#order" style="left:753px;top:2380px">
    <span class="arrow"><svg width="16" height="14" viewBox="0 0 16 14"><path d="M1 7 H14 M8 1 L14 7 L8 13" fill="none" stroke="var(--pink)" stroke-width="2"/></svg></span>Order Now
  </a>

  <!-- Closing -->
  <div class="ph" role="img" aria-label="Friends at a table with a board of mini burgers" style="left:520px;top:2520px;width:680px;height:515px;background:radial-gradient(ellipse at 62% 72%,#a86a3e 0%,#c4987a 28%,#e8d6cc 55%,rgba(255,255,255,0) 80%)"></div>
  <div class="closing-eyebrow">Enjoy</div>
  <h2 class="closing-title heading">Brambles Sandwiches</h2>
  <p class="closing-text">Unfortunately, we can’t open another Brambles, but we can offer you this collection of our recipes for you to try out at home with your family and friends.</p>
  <a class="btn" href="#order" style="left:147px;top:2845px">
    <span class="arrow"><svg width="16" height="14" viewBox="0 0 16 14"><path d="M1 7 H14 M8 1 L14 7 L8 13" fill="none" stroke="var(--pink)" stroke-width="2"/></svg></span>Order Now
  </a>
  <div class="ph" role="img" aria-label="Cheeseburger patty with melted cheese" style="left:-20px;top:2850px;width:140px;height:130px;border-radius:50%;background:radial-gradient(ellipse at 50% 40%,#f0b53a 0%,#d89326 45%,#4a2e1f 80%)"></div>
  <div class="copyright">Copyright 2022. <a href="#">Brambles Sandwiches</a> | All Rights Reserved</div>

</main>
</body>
</html>
```